Yacht, Boats, Watersports company needs a redesign of business card

Hello Designers!
We are a Boat dealership company that sells fun in the water, we sell boats, Yachts, Kayaks and also yacht WaterSport toys. We are looking to redesign our business cards in to something a little bit more sophisticated. in a way that we can make better use of our company colors. I'm attaching a zipped file containing the company 3 sets of company logo which one is an horizontal another one is a vertical and also a chromed 3d logo. Also is included two set of business cards that we use and also some designs that i think it's interesting. We use PMS 2026c Orange and PMS 7687C Blue. I would like to see at least two different options with the orange as accent and also using blue as an accent color. It's really important for the business cards to have a font option and size that is legible to most people. Our current website is wwww.coralpennant.com. Please visit if you want to have a better feeling of the Boat dealership
You can send Single sided or double side options. We are now using single sided but we may be open for a double side option if we really like the design.
Target Market(s)
Marine, boat sales, yacht sales, water toys sales/
Contact Information for Business Card
Name: Dale Whitcombe
Address: 212 North Fenwick Lane,
Dania Beach, FL 33004
Phone: 954-731-8842
Fax: 954:731-8843
Cell: 954-382-1490
Email: dw@coralpennant.com
Website: coralpennant.com
Requirements
Must have
- the current information of the business card provided.
logo
use the PMS Colors
Nice to have
- a touch of elegance and sophistication but simple
Should not have
- should not have any typography that is hard to read, the card should be simple but yet sophisticated.

```html
<!DOCTYPE html>
<html lang="en">
<head>
<meta charset="utf-8">
<title>Coral Pennant – Business Card</title>
<link href="https://fonts.googleapis.com/css2?family=Michroma&family=Work+Sans:wght@400;500&display=swap" rel="stylesheet">
<style>
  :root {
    --blue: #17497f;
    --orange: #f0582a;
    --ink: #3a3a3a;
    --paper: #ffffff;
    --backdrop: #e9eaec;
  }
  * { box-sizing: border-box; margin: 0; padding: 0; }
  html, body { width: 1200px; height: 881px; overflow: hidden; }
  body {
    background: var(--backdrop);
    font-family: "Work Sans", Arial, sans-serif;
    display: flex; flex-direction: column; align-items: center; justify-content: center;
    gap: 48px;
  }
  .card {
    width: 600px; height: 343px; position: relative; overflow: hidden;
    box-shadow: 0 6px 18px rgba(0,0,0,.18);
  }
  /* Front */
  .card-front { background: var(--blue); display: flex; align-items: center; justify-content: center; }
  .brand { display: flex; align-items: center; gap: 16px; }
  .brand-dot { width: 30px; height: 30px; border-radius: 50%; background: var(--orange); }
  .brand-name {
    font-family: "Michroma", Arial, sans-serif; color: var(--paper);
    font-size: 26px; letter-spacing: 2px; text-transform: uppercase;
  }
  /* Back */
  .card-back { background: var(--paper); }
  .identity { position: absolute; left: 30px; top: 134px; width: 258px; text-align: right; }
  .person-name {
    font-family: "Michroma", Arial, sans-serif; color: var(--blue);
    font-size: 16px; font-weight: 400; text-transform: uppercase; letter-spacing: .5px;
    white-space: nowrap; line-height: 1.2;
  }
  .address { color: var(--ink); font-size: 13px; line-height: 1.45; margin-top: 8px; letter-spacing: .4px; }
  .divider { position: absolute; left: 305px; top: 104px; width: 1.5px; height: 112px; background: var(--orange); }
  .contacts { position: absolute; left: 322px; top: 104px; list-style: none; }
  .contacts li {
    display: flex; align-items: center; gap: 8px;
    font-size: 12.5px; color: var(--ink); line-height: 22px; letter-spacing: .4px; white-space: nowrap;
  }
  .contacts svg { width: 11px; height: 11px; flex: none; }
  .web-domain { color: var(--blue); font-weight: 500; }
  .rule-accent { position: absolute; left: 0; right: 0; bottom: 40px; height: 2px; background: var(--orange); }
  .band { position: absolute; left: 0; right: 0; bottom: 0; height: 34px; background: var(--blue); }
</style>
</head>
<body>
  <section class="card card-front">
    <div class="brand">
      <span class="brand-dot"></span>
      <span class="brand-name">Coral Pennant</span>
    </div>
  </section>

  <section class="card card-back">
    <div class="identity">
      <h1 class="person-name">Dale Whitcombe</h1>
      <p class="address">212 North Fenwick Lane,<br>Dania Beach, FL 33004</p>
    </div>
    <span class="divider"></span>
    <ul class="contacts">
      <li><svg viewBox="0 0 12 12"><path d="M2.5 1 4.5 1 5.2 3.6 4 4.6Q5 7 7.4 8L8.4 6.8 11 7.5 11 9.5Q10.5 11 9 11 1 10 1 3 1 1.5 2.5 1Z" fill="var(--orange)"/></svg><span>954-731-8842</span></li>
      <li><svg viewBox="0 0 12 12"><rect x="3" y="1" width="6" height="3" fill="var(--orange)"/><rect x="1" y="4.5" width="10" height="4.5" rx="1" fill="var(--orange)"/><rect x="3" y="8" width="6" height="3" fill="var(--orange)"/></svg><span>954:731-8843</span></li>
      <li><svg viewBox="0 0 12 12"><rect x="3" y="1" width="6" height="10" rx="1" fill="none" stroke="var(--orange)" stroke-width="1.3"/><circle cx="6" cy="9" r=".7" fill="var(--orange)"/></svg><span>954-382-1490</span></li>
      <li><svg viewBox="0 0 12 12"><rect x="1" y="2.5" width="10" height="7" fill="none" stroke="var(--orange)" stroke-width="1.2"/><path d="M1 2.5 6 6.5 11 2.5" fill="none" stroke="var(--orange)" stroke-width="1.2"/></svg><span>dw@coralpennant.com</span></li>
      <li><svg viewBox="0 0 12 12"><circle cx="6" cy="6" r="5" fill="none" stroke="var(--orange)" stroke-width="1.1"/><ellipse cx="6" cy="6" rx="2.2" ry="5" fill="none" stroke="var(--orange)" stroke-width="1"/><path d="M1 6H11" stroke="var(--orange)" stroke-width="1"/></svg><span>www.<span class="web-domain">coralpennant</span>.com</span></li>
    </ul>
    <span class="rule-accent"></span>
    <span class="band"></span>
  </section>
</body>
</html>
```